Quorbelline.io - Please redesign to make it look better from current design

We already have the current website, that you can access but we think it can improve from current version.
Quorbelline is a cryptocurrency hedge fund that allow you to participate in the hedge fund with cryptocurrency such as eth.
At current phase, we are doing an ICO, then we want to make sure that the website it looks professional, beautiful and trustable enough for investors after looking at our website.
Target Market(s)
Investors
Industry/Entity Type
Investment
Coding
Coded - Design and coding required
Number of Pages Required
1 page
Look and feel
Each slider illustrates characteristics of the customer's brand and the style your logo design should communicate.

```html
<!DOCTYPE html>
<html lang="en">
<head>
<meta charset="utf-8">
<title>Quorbelline.io – Digital Asset Management</title>
<link rel="stylesheet" href="https://fonts.googleapis.com/css2?family=Poppins:wght@300;400;500;600&family=Raleway:wght@400;500;700&display=swap">
<style>
:root{
  --navy:#1b2a8e;
  --royal:#2a3db0;
  --hero-a:#3347b9;
  --hero-b:#2436a0;
  --sky:#c8ecf9;
  --bar:#7fd4f6;
  --ink:#1f2330;
  --grey:#5b5f6b;
  --white:#ffffff;
  --mist:#eef0f4;
  --accent:#ee7a3b;
}
*{box-sizing:border-box;margin:0;padding:0}
html,body{width:1200px;height:3651px;overflow:hidden;background:var(--white)}
body{font-family:"Raleway",sans-serif;color:var(--ink)}
.page{position:relative;width:1200px;height:3651px;overflow:hidden}
.backdrop{position:absolute;inset:0}
.abs{position:absolute}
.logo{display:flex;align-items:center;gap:12px;font-family:"Poppins",sans-serif;font-weight:500;color:var(--white)}
.logo .dot{width:40px;height:40px;border-radius:50%;background:var(--white)}
.nav{left:510px;top:46px;width:690px;display:flex;gap:0;font-family:"Poppins",sans-serif;font-size:16px;color:var(--white);letter-spacing:.5px}
.nav span{position:absolute;top:0}
.nav-line{left:510px;top:114px;width:690px;height:1px;background:rgba(255,255,255,.35)}
.nav-active{left:530px;top:112px;width:66px;height:3px;background:var(--white)}
.hero-visual{left:650px;top:110px;width:550px;height:560px;background:radial-gradient(ellipse at 55% 55%,rgba(150,190,255,.55),rgba(60,80,190,.15) 60%,rgba(40,55,160,0) 75%)}
.hero-title{left:80px;top:270px;font-family:"Poppins",sans-serif;font-weight:300;font-size:92px;color:var(--white);line-height:1}
.hero-sub{left:80px;top:395px;font-family:"Poppins",sans-serif;font-weight:400;font-size:39px;color:var(--white)}
.hero-text{left:80px;top:458px;width:620px;font-size:19px;line-height:26px;color:var(--white)}
.section-title{width:1200px;left:0;text-align:center;font-family:"Poppins",sans-serif;font-weight:400;font-size:40px;letter-spacing:1px}
.about-text{left:140px;top:893px;width:920px;text-align:center;font-size:15px;line-height:24px;color:var(--grey)}
.btn{display:flex;align-items:center;justify-content:center;border-radius:30px;font-family:"Poppins",sans-serif;font-weight:500;font-size:14px;color:var(--white);letter-spacing:.5px}
.btn-gradient{background:linear-gradient(90deg,#b9dcf4,var(--royal) 60%,var(--navy))}
.btn-outline{background:linear-gradient(90deg,#5d6fd0,var(--royal));box-shadow:0 0 0 4px rgba(255,255,255,.3)}
.process-visual{left:183px;top:1400px;width:340px;height:305px;border-radius:12px;background:linear-gradient(160deg,rgba(255,255,255,.18),rgba(255,255,255,.05))}
.model-title{left:625px;top:1408px;font-family:"Poppins",sans-serif;font-size:27px;color:var(--white)}
.model-text{left:625px;top:1462px;width:520px;font-size:16.5px;line-height:25px;color:var(--white)}
.dist-title{left:0;width:1200px;top:1903px;text-align:center;font-family:"Poppins",sans-serif;font-size:26px;color:var(--ink)}
.dist-sub{left:0;width:1200px;top:1945px;text-align:center;font-size:16px;color:var(--grey)}
.dist-label{font-size:16px;color:var(--grey);white-space:nowrap}
.member-photo{width:156px;height:156px;border-radius:50%;background:radial-gradient(circle at 50% 40%,#8a6f5f,#3b3e52 75%);border:3px solid var(--white)}
.member-name{font-family:"Poppins",sans-serif;font-size:25px;color:var(--navy);white-space:nowrap}
.member-role{font-size:15px;font-weight:700;color:var(--ink)}
.member-bio{width:320px;font-size:14px;line-height:21px;color:var(--grey)}
.info-card{left:78px;top:3140px;width:1044px;height:255px;background:var(--white);border-radius:6px;box-shadow:0 10px 30px rgba(20,40,120,.15)}
.footer-col{font-size:16px;line-height:24px;color:var(--white)}
.social{width:50px;height:50px;border-radius:50%;border:2px solid rgba(255,255,255,.8)}
.social.fill{background:#5a82d8;border-color:#5a82d8}
</style>
</head>
<body>
<div class="page">
  <svg class="backdrop" width="1200" height="3651" viewBox="0 0 1200 3651" aria-hidden="true">
    <defs>
      <linearGradient id="heroGrad" x1="0" y1="0" x2="1" y2="1">
        <stop offset="0" stop-color="#3b4fc2"/>
        <stop offset="1" stop-color="#22339c"/>
      </linearGradient>
      <linearGradient id="mistGrad" x1="0" y1="0" x2="0" y2="1">
        <stop offset="0" stop-color="#ffffff"/>
        <stop offset="1" stop-color="#e7e9ee"/>
      </linearGradient>
    </defs>
    <rect x="0" y="0" width="1200" height="900" fill="url(#heroGrad)"/>
    <polygon points="0,850 1200,585 1200,1300 0,1300" fill="url(#mistGrad)"/>
    <polygon points="0,1265 1200,1080 1200,1690 0,1940" fill="#1d2c93"/>
    <polygon points="0,2507 1200,2264 1200,3651 0,3651" fill="#c8ecf9"/>
    <g fill="#7fd4f6">
      <rect x="80" y="3075" width="22" height="65"/><rect x="112" y="3090" width="22" height="50"/>
      <rect x="144" y="3062" width="22" height="78"/><rect x="190" y="3112" width="22" height="28"/>
      <rect x="226" y="3085" width="22" height="55"/><rect x="262" y="3120" width="22" height="20"/>
      <rect x="300" y="3098" width="22" height="42"/><rect x="336" y="3115" width="22" height="25"/>
      <rect x="372" y="3082" width="22" height="58"/><rect x="412" y="3103" width="22" height="37"/>
      <rect x="448" y="3075" width="22" height="65"/><rect x="490" y="3110" width="22" height="30"/>
      <rect x="528" y="3095" width="22" height="45"/><rect x="566" y="3108" width="22" height="32"/>
      <rect x="590" y="3065" width="22" height="75"/><rect x="634" y="3090" width="22" height="50"/>
      <rect x="672" y="3105" width="22" height="35"/><rect x="710" y="3080" width="22" height="60"/>
      <rect x="748" y="3115" width="22" height="25"/><rect x="786" y="3095" width="22" height="45"/>
      <rect x="826" y="3108" width="22" height="32"/><rect x="864" y="3085" width="22" height="55"/>
      <rect x="902" y="3118" width="22" height="22"/><rect x="940" y="3100" width="22" height="40"/>
      <rect x="988" y="3080" width="22" height="60"/><rect x="1024" y="3095" width="22" height="45"/>
      <rect x="1062" y="3072" width="22" height="68"/><rect x="1098" y="3060" width="22" height="80"/>
    </g>
    <polygon points="0,3395 1200,3237 1200,3651 0,3651" fill="#1b2a8e"/>
    <polyline points="586,655 600,668 614,655" fill="none" stroke="#ffffff" stroke-width="3"/>
  </svg>

  <header>
    <div class="abs logo" style="left:80px;top:40px;font-size:16px"><span class="dot"></span>quorbelline</div>
    <nav class="abs nav" aria-label="Main">
      <span style="left:30px">HOME</span>
      <span style="left:135px">ABOUT</span>
      <span style="left:250px">PROCESS</span>
      <span style="left:383px">OUR TEAM</span>
      <span style="left:525px">CONTACT</span>
    </nav>
    <div class="abs nav-line"></div>
    <div class="abs nav-active"></div>
  </header>

  <section class="hero">
    <div class="abs hero-visual" role="img" aria-label="Hands using a transparent touch tablet showing asset management"></div>
    <h1 class="abs hero-title">quorbelline</h1>
    <p class="abs hero-sub">Digital Asset Management</p>
    <p class="abs hero-text">Quorbelline enable companies and investors to facilities business operation in modern digital world, including asset management on hedge fund strategy model.</p>
  </section>

  <section class="about">
    <h2 class="abs section-title" style="top:820px;color:var(--ink)">ABOUT US</h2>
    <p class="abs about-text">Quorbelline process and manages on hedge fund strategy models which invests in a diversified portfolio of blockchain tokens. Blockchain tokens are emerging which add a monetary incentive layer to p2p protocols and facilitate equity crowdfunding that anyone in the world can participate in. This means open source software developers can monetize their networks at the protocol level and users of the network are the equity owners of the network. For this conditions, returns will go to holders of the tokens.</p>
    <div class="abs btn btn-gradient" style="left:518px;top:1053px;width:164px;height:50px">READ MORE</div>
  </section>

  <section class="process">
    <h2 class="abs section-title" style="top:1310px;color:var(--white)">PROCESS</h2>
    <div class="abs process-visual" role="img" aria-label="Line illustration of a rocket launching from a laptop with charts and gears"></div>
    <h3 class="abs model-title">Hedge Fund Model</h3>
    <p class="abs model-text">Quorbelline run on closed-end fund (CEF) model which offers its shares to investors and utilize the fund to speculate and invest in the innovative blockchain tokens. Quorbelline will charge an upfront annual operation fee 4% of the money raised during the ICO. After that, the fund will charge a quarterly performance of 50% on the net profit made.</p>
    <div class="abs btn btn-outline" style="left:622px;top:1636px;width:168px;height:56px">EXPLORE MORE</div>
  </section>

  <section class="distribution">
    <h3 class="abs dist-title">Net Profit Distribution</h3>
    <p class="abs dist-sub">The remainder (50% minus performance fee, so at least 35%) is reinvested</p>
    <svg class="abs" style="left:440px;top:1995px" width="320" height="300" viewBox="0 0 320 300" aria-hidden="true">
      <defs>
        <radialGradient id="discGrad" cx="0.5" cy="0.45" r="0.6">
          <stop offset="0" stop-color="#ffffff"/>
          <stop offset="1" stop-color="#d6d9e0"/>
        </radialGradient>
      </defs>
      <circle cx="159" cy="147" r="127" fill="url(#discGrad)"/>
      <text x="159" y="155" text-anchor="middle" font-family="Poppins, sans-serif" font-size="26" font-weight="500" fill="#1b2a8e">quorbelline</text>
      <g fill="#1b2a8e">
        <circle cx="66" cy="45" r="6"/><circle cx="259" cy="45" r="6"/>
        <circle cx="35" cy="179" r="6"/><circle cx="283" cy="179" r="6"/>
        <circle cx="159" cy="274" r="6"/>
      </g>
    </svg>
    <p class="abs dist-label" style="right:713px;top:2030px">50 % of net profit is distributed to investors</p>
    <p class="abs dist-label" style="left:718px;top:2030px">&gt; 15% net profit &gt; 15% performance fee</p>
    <p class="abs dist-label" style="right:745px;top:2163px">0 – 5 % net profit &gt; 0% performance fee</p>
    <p class="abs dist-label" style="left:747px;top:2163px">10-15 % net profit &gt; 13% performance fee</p>
    <p class="abs dist-label" style="left:0;width:1200px;text-align:center;top:2280px">5 – 10% net profit &gt; 5% performance fee</p>
  </section>

  <section class="team">
    <h2 class="abs section-title" style="top:2497px;color:var(--ink)">EXECUTIVE TEAM</h2>

    <div class="abs member-photo" style="left:78px;top:2575px" role="img" aria-label="Portrait of the director"></div>
    <h4 class="abs member-name" style="left:80px;top:2757px">Dalvren Okotsu</h4>
    <p class="abs member-role" style="left:80px;top:2806px">Director</p>
    <p class="abs member-bio" style="left:80px;top:2840px">&nbsp;As a hedge fund manager, Okotsu is the Chief Executive Officer of Fennick Ridge Capital LLC, an investment manager of Coldwater Vale Fund SP (Long-Short Equity Fund, investing in U.S. Stock Market) and Lumen Arc Fund (Managed Futures Fund, focusing in Japanese Futures Market) Both based in Tokyo.</p>

    <div class="abs member-photo" style="left:433px;top:2575px" role="img" aria-label="Portrait of the technical advisor"></div>
    <h4 class="abs member-name" style="left:433px;top:2757px">Telmar Visquet</h4>
    <p class="abs member-role" style="left:433px;top:2806px">Technical advisor</p>
    <p class="abs member-bio" style="left:433px;top:2840px">Visquet has various experienced on cryptocurrency and blockchain technology. He created what was the world's 4th most valuable cryptocurrency in February 2014. He is also the world's first person to implement stealth addresses in Pellow-Wallets, improving cryptocurrency anonymity.</p>

    <div class="abs member-photo" style="left:789px;top:2575px" role="img" aria-label="Portrait of the marketing consultant"></div>
    <h4 class="abs member-name" style="left:791px;top:2757px">Oriel Kanthavong</h4>
    <p class="abs member-role" style="left:791px;top:2806px">Marketing Consultant</p>
    <p class="abs member-bio" style="left:791px;top:2840px">Kanthavong embeds a decade of experience in brand building, strategic planning, and marketing communication across the global agencies, such as Harrowgate Group, Velmont, Corbel &amp; Finch, Sanmira. His seasoned specialty focuses on exploring a new market insight to formulate disruptive strategies.</p>
  </section>

  <section class="abs info-card">
    <h2 class="abs section-title" style="left:0;width:1044px;top:48px;color:var(--ink)">FOR MORE INFORMATION</h2>
    <div class="abs btn btn-gradient" style="left:384px;top:137px;width:273px;height:62px">DOWNLOAD WHITEPAPER</div>
  </section>

  <footer>
    <div class="abs logo" style="left:128px;top:3478px;font-size:22px"><span class="dot" style="width:52px;height:52px"></span>quorbelline</div>
    <div class="abs footer-col" style="left:365px;top:3440px;width:250px">
      <p style="font-family:'Poppins',sans-serif;letter-spacing:3px;margin-bottom:12px">quorbelline</p>
      <p style="font-size:15px;line-height:23px">Suite 12-18, 9B/F, East Tower, Meridian Trade Centre, Harbour Point, 42 Lantern Road, Kowloon Bay, Hong Kong.</p>
    </div>
    <div class="abs footer-col" style="left:650px;top:3446px;font-weight:700;font-size:15px;line-height:38px">
      <p>Privacy Policy</p>
      <p>Cookie</p>
    </div>
    <div class="abs social fill" style="left:868px;top:3452px"></div>
    <div class="abs social" style="left:936px;top:3452px"></div>
    <div class="abs social" style="left:1000px;top:3452px"></div>
    <p class="abs footer-col" style="left:860px;top:3522px;width:230px;font-size:15px">© <b>quorbelline</b> - 2017. All Rights Reserved.</p>
  </footer>
</div>
</body>
</html>
```